Life Coaching business needs a new flyer

We are an Australian business that specialises in Life Coaching, Career Coaching, Health and Wellness Coaching, Yoga and Pilates. We need a A4 double sided flyer that is full colour and folded to DL format. I have attached a couple of designs that I like and some pictures and would like the flyer to be bright yet stylish.

Industry/Entity Type

Life Coaching

```html
<!DOCTYPE html>
<html lang="en">
<head>
<meta charset="utf-8">
<title>Clearwater Coaching – DL Brochure</title>
<link href="https://fonts.googleapis.com/css2?family=Cinzel:wght@400;600&family=Open+Sans:wght@400;600&display=swap" rel="stylesheet">
<style>
:root{
  --blue:#1b98d5;
  --blue-dark:#0f74b0;
  --green:#5cb82b;
  --green-dark:#3f9a1c;
  --ink:#2b2b2b;
  --paper:#ffffff;
  --mist:#eaf5fa;
  --aqua:#d6eef4;
  --stage:#e4e4e4;
}
*{box-sizing:border-box;margin:0;padding:0}
html,body{width:920px;height:1200px;overflow:hidden}
body{background:var(--stage);font-family:"Open Sans",Arial,sans-serif;color:var(--ink);position:relative}
.sheet{position:absolute;left:60px;width:800px;height:566px;display:flex;box-shadow:0 4px 14px rgba(0,0,0,.18);background:var(--paper)}
.sheet--outside{top:24px}
.sheet--inside{top:610px}
.panel{position:relative;width:266.67px;height:100%;overflow:hidden}
.panel + .panel{border-left:1px solid rgba(0,0,0,.06)}
.photo{position:absolute}
.tab{position:absolute;display:inline-block;font-family:"Cinzel",Georgia,serif;color:#fff;font-size:11px;letter-spacing:.5px;padding:3px 16px 3px 10px;border-radius:0 14px 14px 0}
.tab--green{background:var(--green)}
.tab--blue{background:var(--blue)}
.brand{display:flex;align-items:center;gap:7px;font-family:"Cinzel",Georgia,serif;color:var(--blue);font-weight:600}
.brand__dot{width:14px;height:14px;border-radius:50%;background:var(--green);flex:none}

/* testimonials */
.testimonials{background:var(--blue);color:#fff}
.testimonials .tab{top:22px;left:0}
.quotes{position:absolute;top:52px;left:16px;right:14px;font-size:8.3px;line-height:1.32}
.quote{margin-bottom:5px}
.quote b{font-size:13px;line-height:0;vertical-align:-3px;margin-right:2px}
.quote__name{display:block;font-family:"Cinzel",Georgia,serif;font-size:11px;margin-top:2px;letter-spacing:.4px}
.testimonials .photo{left:0;bottom:0;width:100%;height:160px;background:linear-gradient(160deg,#f3c98a 0%,#d98f55 45%,#3f7aa6 100%);border-top:6px solid var(--green);border-top-left-radius:100% 70%}

/* intro */
.intro{background:var(--paper)}
.intro__text{position:absolute;top:20px;left:18px;right:16px;font-size:8.3px;line-height:1.4}
.intro__text p{margin-bottom:6px}
.contact{position:absolute;top:104px;left:22px;font-size:9px;font-weight:600;line-height:1.75}
.contact li{list-style:none;display:flex;align-items:center;gap:6px}
.contact svg{width:10px;height:10px;flex:none}
.intro .photo{top:168px;left:63px;width:140px;height:140px;border-radius:50%;border:5px solid var(--green);background:linear-gradient(135deg,#3a2a22,#b98c70 55%,#e9ddd2)}
.offer{position:absolute;top:320px;left:0;width:100%;text-align:center}
.offer__title{font-family:"Cinzel",Georgia,serif;color:var(--blue);font-size:17px;line-height:1.12}
.offer__sub{font-family:"Cinzel",Georgia,serif;color:var(--green-dark);font-size:10.5px;margin-top:5px}
.offer__note{font-size:9px;margin-top:2px}
.intro .brand{position:absolute;top:435px;left:0;width:100%;flex-direction:column;gap:6px;font-size:14px;text-align:center;line-height:1.15}
.intro .brand__dot{width:52px;height:52px}

/* cover */
.cover{background:var(--paper)}
.cover .brand{position:absolute;top:18px;left:22px;font-size:13px}
.cover .brand__dot{width:22px;height:22px}
.circle{position:absolute;border-radius:50%;display:flex;justify-content:center;font-family:"Cinzel",Georgia,serif;font-size:11px;text-align:center}
.circle--coach{top:52px;left:58px;width:118px;height:118px;border:5px solid var(--green);background:linear-gradient(180deg,#2d8fd1,#9fd0ef);color:#fff;padding-top:16px;font-size:10px}
.circle--med{top:138px;left:66px;width:150px;height:150px;border:6px solid var(--blue);background:linear-gradient(180deg,#fafdff 0%,#8fc7ea 50%,#7fb86a 100%);padding-top:20px;color:var(--ink)}
.circle--yoga{top:240px;left:34px;width:222px;height:222px;border:7px solid var(--green);background:linear-gradient(180deg,#f7f9fb 0%,#cfe2ee 55%,#8fb8d2 100%);padding-top:30px;color:var(--ink);font-size:13px}
.cover__band{position:absolute;left:0;bottom:0;width:100%;height:170px;background:var(--blue);clip-path:ellipse(130% 100% at 80% 100%)}
.cover__url{position:absolute;bottom:14px;right:14px;color:#fff;font-size:10px}

/* inside left */
.welcome{background:var(--paper)}
.questions{position:absolute;top:22px;left:14px;right:12px;font-size:9.2px;line-height:1.35;font-weight:600}
.questions p{margin-bottom:3px}
.answer{position:absolute;top:108px;left:14px;font-family:"Cinzel",Georgia,serif;color:var(--blue);font-size:12.5px}
.welcome .photo{top:136px;left:0;width:100%;height:180px;background:linear-gradient(180deg,#fff 0%,#f1ebe6 40%,#c8a78f 75%,#fff 100%)}
.mission{position:absolute;left:0;bottom:0;width:100%;height:250px;background:var(--green);border-top:6px solid var(--blue);border-top-left-radius:70% 40%;color:#fff;padding:40px 14px 0 20px}
.mission__title{font-family:"Cinzel",Georgia,serif;font-size:18px;line-height:1.02;margin-bottom:10px}
.mission__title span{display:block;font-size:13px}
.mission p{font-size:8.8px;line-height:1.4;margin-bottom:6px}

/* inside middle & right */
.services,.help{background:linear-gradient(180deg,#f4fafc 0%,var(--aqua) 55%,#e9f6f9 100%)}
.block{position:absolute;left:0;width:100%;font-size:8.4px;line-height:1.4}
.block .tab{position:relative;margin-bottom:6px}
.block p{padding:0 14px 0 16px}
.services .b1{top:20px}
.services .b2{top:162px}
.services .b3{top:298px}
.services .photo{border-radius:50%;border:5px solid var(--green)}
.services .p1{left:8px;bottom:40px;width:106px;height:106px;background:linear-gradient(180deg,#a7d6ef,#f3efe8)}
.services .p2{left:116px;bottom:10px;width:126px;height:126px;border-color:var(--blue);background:linear-gradient(180deg,#bfe5f5,#e66aa2 70%,#c8d86a)}
.help .b1{top:20px}
.help .b2{top:236px}
.help .b3{top:302px}
.needs{list-style:none;padding:2px 14px 0 20px}
.needs li{position:relative;padding-left:10px}
.needs li::before{content:"";position:absolute;left:0;top:4px;width:5px;height:5px;border-radius:50%;background:var(--blue)}
.help .brand{position:absolute;top:378px;right:14px;font-size:9px;flex-direction:column;gap:3px}
.help .brand__dot{width:20px;height:20px}
.help .photo{border-radius:50%}
.help .p1{left:-10px;bottom:-10px;width:170px;height:170px;border:6px solid var(--green);background:linear-gradient(135deg,#f6d08a,#e39a55 50%,#b56a44)}
.help .p2{right:-30px;bottom:20px;width:120px;height:120px;border:5px solid var(--blue);background:linear-gradient(135deg,#9fcfe8,#e8c6a6 60%,#7a6b5c)}
</style>
</head>
<body>

<section class="sheet sheet--outside" aria-label="Outside of brochure">
  <div class="panel testimonials">
    <span class="tab tab--green">Happy Clients Testimonials</span>
    <div class="quotes">
      <div class="quote"><b>“</b>I have lost 10 kilos and now have the energy to play with my kids. Thanks Mara for your support, guidance and helping me get rid of my limiting beliefs. I feel I can achieve anything now! The sky's the limit.<b>”</b><span class="quote__name">Leah, Mosman</span></div>
      <div class="quote"><b>“</b>I had always wanted to start up my own café however every time it came to putting it into practice I would procrastinate and not achieve anything. I became overwhelmed with the whole process and never achieved anything. Mara put it into bite sized chunks and helped me set small achievable goals. I am now a happy café owner.<b>”</b><span class="quote__name">Nora, Double Bay</span></div>
      <div class="quote"><b>“</b>Mara has helped me to change my life around in all aspects. I would have been lost without her. Thanks Mara for your professionalism, support and guidance.<b>”</b><span class="quote__name">Bella, Cremorne</span></div>
      <div class="quote"><b>“</b>I was so busy with kids, work and my husband I lost who I was. Mara has helped me find the person again.<b>”</b><span class="quote__name">Sophie, Chatswood</span></div>
      <div class="quote"><b>“</b>When I started with Coach Mara, I didn't know anything about coaching. I called her because she helped a friend of mine make a career change that was a perfect fit for her. I had the opportunity to make a change too and did not know where to start. I am now in a job that I love. I would recommend Mara to everyone.<b>”</b><span class="quote__name">Jonah, Texas America</span></div>
    </div>
    <div class="photo" role="img" aria-label="Photo of happy friends celebrating outdoors by the sea at sunset"></div>
  </div>

  <div class="panel intro">
    <div class="intro__text">
      <p>Clearwater Coaching and Meditation Studio is a professional service that can help you achieve the goals that you are looking for in Life Coaching, Meditation, and Yoga/Pilates.</p>
      <p>If you are ready to take your life to the next level and would like to know more, please contact us.</p>
    </div>
    <ul class="contact">
      <li><svg viewBox="0 0 10 10"><circle cx="5" cy="5" r="5" fill="#5cb82b"/><path d="M3 2.5l1 1-.6.8c.4.9 1 1.5 1.9 1.9l.8-.6 1 1-.7.9C4.5 7.3 2.7 5.5 2.5 3.2z" fill="#fff"/></svg>02 5550 1842</li>
      <li><svg viewBox="0 0 10 10"><circle cx="5" cy="5" r="5" fill="#5cb82b"/><rect x="2.4" y="3.2" width="5.2" height="3.6" fill="#fff"/><path d="M2.4 3.2L5 5.2l2.6-2" stroke="#5cb82b" stroke-width=".6" fill="none"/></svg>info@clearwatercoaching.com.au</li>
      <li><svg viewBox="0 0 10 10"><circle cx="5" cy="5" r="5" fill="#5cb82b"/><circle cx="5" cy="5" r="2.6" fill="none" stroke="#fff" stroke-width=".7"/><path d="M2.4 5h5.2M5 2.4v5.2" stroke="#fff" stroke-width=".6"/></svg>www.clearwatercoaching.com.au</li>
    </ul>
    <div class="photo" role="img" aria-label="Portrait photo of the two coaches"></div>
    <div class="offer">
      <div class="offer__title">Free Introductory<br>Life Coaching</div>
      <div class="offer__sub">Phone/Video Session - 20 mins</div>
      <div class="offer__note">(To see if coaching is right for you)</div>
    </div>
    <div class="brand"><span class="brand__dot"></span><span>Clearwater Coaching<br>and Meditation Studio</span></div>
  </div>

  <div class="panel cover">
    <div class="brand"><span class="brand__dot"></span><span>Clearwater Coaching</span></div>
    <div class="cover__band"></div>
    <div class="circle circle--coach" role="img" aria-label="Photo of a signpost pointing to career, family, health and friends">Life Coaching</div>
    <div class="circle circle--med" role="img" aria-label="Photo of a group meditating on grass">Meditation</div>
    <div class="circle circle--yoga" role="img" aria-label="Photo of two people doing yoga on a beach">Yoga/Pilates</div>
    <div class="cover__url">www.clearwatercoaching.com.au</div>
  </div>
</section>

<section class="sheet sheet--inside" aria-label="Inside of brochure">
  <div class="panel welcome">
    <div class="questions">
      <p>Are you looking at making changes this year?</p>
      <p>Are you stuck in a rut or at a crossroad in your life?</p>
      <p>Are you wanting to lose weight but can't get motivated?</p>
      <p>Do you have ongoing problems with your career, relationships, or just life itself?</p>
    </div>
    <div class="answer">Life Coaching is the answer</div>
    <div class="photo" role="img" aria-label="Photo of a cheerful group of people celebrating"></div>
    <div class="mission">
      <div class="mission__title">Clearwater Coaching<span>and Meditation Studio</span></div>
      <p>Our mission is to help you become the best possible person you can be. Mentally, physically, and spiritually.</p>
      <p>We offer highly qualified and compassionate trainers/coaches for Life Coaching, Meditation, Yoga and Pilates.</p>
      <p>They will guide and motivate you every step of the way to achieve all your dreams and goals.</p>
      <p>They will make you be the best you can be. Happy</p>
    </div>
  </div>

  <div class="panel services">
    <div class="block b1">
      <span class="tab tab--blue">Life Coaching</span>
      <p>Your Life Coach will give you the confidence and the ability to move forward in a positive manner in all areas of your life where you crave change.</p>
      <p style="margin-top:5px">Life Coaching is about breaking down the barriers preventing this change from happening, and creating the ideal environment for positive action to take place. It is a holistic approach, which looks at the present and sets goals for a totally successful future.</p>
    </div>
    <div class="block b2">
      <span class="tab tab--blue">Career Coaching</span>
      <p>Are you at a crossroads in your career and at a loss about what to do next? Do you want your work to be in alignment with the authentic you? It can be difficult to assess career options, goals, and strategies, and have the confidence to implement changes on your own. With the right coaching support, you will gain the clarity that you need to take control and have a fulfilling and rewarding career.</p>
    </div>
    <div class="block b3">
      <span class="tab tab--blue">Wellness Coaching</span>
      <p>Health and wellness coaches help their clients find the motivation and tools to achieve their health and wellness goals, working with the client to examine and improve the psychological framework that supports those goals.</p>
    </div>
    <div class="photo p1" role="img" aria-label="Photo of a woman stretching on a beach"></div>
    <div class="photo p2" role="img" aria-label="Photo of a joyful woman in a convertible car"></div>
  </div>

  <div class="panel help">
    <div class="block b1">
      <span class="tab tab--green">Why would I need help?</span>
      <p>Coaching is for anyone who wants to make lasting changes in their life.</p>
      <p>Coaching can assist with such issues as:</p>
      <ul class="needs">
        <li>Creating a better work-life balance</li>
        <li>Resolving relationship issues</li>
        <li>Career guidance</li>
        <li>Stress management</li>
        <li>Weight loss and fitness</li>
        <li>Motivation and goal setting</li>
        <li>Boosting your self esteem</li>
        <li>Overcoming negative emotions and thoughts</li>
        <li>Better time management</li>
      </ul>
    </div>
    <div class="block b2">
      <span class="tab tab--green">Meditation</span>
      <p>We specialise in teaching meditation from beginners to advanced and teach a variety of techniques for stress reduction, peace of mind, stillness, and clarity.</p>
    </div>
    <div class="block b3">
      <span class="tab tab--green">Yoga/Pilates</span>
      <p>Your highly qualified and experienced Yoga or Pilates instructor will come to you and create a fun and varied workout based on what you enjoy and what your goals are.</p>
    </div>
    <div class="brand"><span class="brand__dot"></span><span>Clearwater Coaching</span></div>
    <div class="photo p2" role="img" aria-label="Photo of an older couple relaxing by the water"></div>
    <div class="photo p1" role="img" aria-label="Photo of a mother hugging her daughter in sunlight"></div>
  </div>
</section>

</body>
</html>
```